BOLD & MINIMALIST DESIGN NEEDED

We want a very bold but minimalistic business card design that is impactful and utilizes both sides of the business card. Our current logo is included for your use.

We want bold fonts and good use of negative space. We don't want the logo to overpower the design.

Target Market(s)

Professionals who are building new commercial buildings.

Industry/Entity Type

Construction

Contact Information for Business Card

Name, Title, email, office phone, cell phone, website

Font styles to use
Serif
Sans Serif

Requirements
Must have
• Bold design!

```html
<!DOCTYPE html>
<html lang="en">
<head>
<meta charset="utf-8">
<title>Ridgeline Design + Build — Business Card</title>
<link rel="stylesheet" href="https://fonts.googleapis.com/css2?family=Montserrat:wght@400;500;700;800&display=swap">
<style>
  :root {
    --stage: #262626;
    --green: #86c443;
    --green-dark: #76b336;
    --ink: #0d0d0d;
    --paper: #ffffff;
    --card-w: 540px;
    --card-h: 309px;
  }
  * { box-sizing: border-box; margin: 0; padding: 0; }
  html, body {
    width: 1200px; height: 689px; overflow: hidden;
    background: var(--stage);
    font-family: "Montserrat", Arial, sans-serif;
  }
  .stage {
    width: 1200px; height: 689px;
    display: flex; align-items: center; justify-content: center; gap: 40px;
  }
  .card {
    position: relative;
    width: var(--card-w); height: var(--card-h);
    border-radius: 22px; overflow: hidden;
    box-shadow: 0 18px 40px rgba(0,0,0,.45);
  }

  /* Front */
  .card--front {
    background: linear-gradient(115deg, #a3d46f 0%, var(--green) 30%, var(--green-dark) 100%);
    display: flex; align-items: center; justify-content: center;
  }
  .wordmark {
    display: flex; align-items: center; gap: 16px;
    color: var(--paper); font-weight: 800; text-transform: uppercase;
  }
  .wordmark__square { width: 38px; height: 38px; background: var(--paper); }
  .wordmark__text { display: flex; flex-direction: column; line-height: 1; }
  .wordmark__name { font-size: 52px; letter-spacing: 0.5px; }
  .wordmark__tag { font-size: 17px; letter-spacing: 7px; margin-top: 8px; }

  /* Back */
  .card--back { background: var(--paper); }
  .card__swoosh { position: absolute; inset: 0; }
  .card__accent-bar {
    position: absolute; right: 0; top: 22px;
    width: 12px; height: 46px; background: var(--green);
  }
  .person {
    position: absolute; right: 30px; top: 24px; text-align: right;
  }
  .person__name {
    color: var(--green); font-weight: 800; font-size: 28px; letter-spacing: 0.5px; line-height: 1.15;
  }
  .person__title {
    color: var(--ink); font-weight: 500; font-size: 12px; letter-spacing: 0.8px; margin-top: 4px;
  }
  .wordmark--back {
    position: absolute; left: 34px; top: 150px; color: var(--ink); gap: 10px;
  }
  .wordmark--back .wordmark__square { width: 24px; height: 24px; background: var(--ink); }
  .wordmark--back .wordmark__name { font-size: 32px; }
  .wordmark--back .wordmark__tag { font-size: 11px; letter-spacing: 4.5px; margin-top: 5px; }

  .contact {
    position: absolute; right: 26px; top: 140px;
    list-style: none; text-align: right; color: var(--paper);
    font-size: 12.5px; line-height: 1.45;
  }
  .contact li { display: flex; justify-content: flex-end; align-items: center; gap: 7px; }
  .contact .contact__address { margin-bottom: 8px; }
  .contact__icon { width: 12px; height: 12px; fill: var(--green); flex: none; }
  .contact__spacer { display: inline-block; width: 12px; }
</style>
</head>
<body>
<main class="stage">

  <section class="card card--front" aria-label="Card front">
    <div class="wordmark">
      <span class="wordmark__square"></span>
      <span class="wordmark__text">
        <span class="wordmark__name">Ridgeline</span>
        <span class="wordmark__tag">Design + Build</span>
      </span>
    </div>
  </section>

  <section class="card card--back" aria-label="Card back">
    <svg class="card__swoosh" viewBox="0 0 540 309" preserveAspectRatio="none" aria-hidden="true">
      <path transform="translate(-10,-12)" d="M560,86 C440,88 385,110 350,160 C310,225 250,292 110,312 L110,340 L560,340 Z" fill="#86c443"/>
      <path transform="translate(-5,-6)" d="M560,86 C440,88 385,110 350,160 C310,225 250,292 110,312 L110,340 L560,340 Z" fill="#ffffff"/>
      <path d="M560,86 C440,88 385,110 350,160 C310,225 250,292 110,312 L110,340 L560,340 Z" fill="#0d0d0d"/>
    </svg>

    <span class="card__accent-bar"></span>

    <div class="person">
      <p class="person__name">ARJUN MEHTA</p>
      <p class="person__title">OWNER-CEO</p>
    </div>

    <div class="wordmark wordmark--back">
      <span class="wordmark__square"></span>
      <span class="wordmark__text">
        <span class="wordmark__name">Ridgeline</span>
        <span class="wordmark__tag">Design + Build</span>
      </span>
    </div>

    <ul class="contact">
      <li>Your address, City<span class="contact__spacer"></span></li>
      <li class="contact__address">State, Zip 1234<span class="contact__spacer"></span></li>
      <li>123 456 789
        <svg class="contact__icon" viewBox="0 0 24 24"><path d="M3 9c0-3 4-5 9-5s9 2 9 5l-4 2-2-3H9L7 11 3 9zm3 4h12l2 7H4l2-7zm6 1.5a2.5 2.5 0 100 5 2.5 2.5 0 000-5z"/></svg>
      </li>
      <li>123 456 789
        <svg class="contact__icon" viewBox="0 0 24 24"><path d="M7 1h10a2 2 0 012 2v18a2 2 0 01-2 2H7a2 2 0 01-2-2V3a2 2 0 012-2zm0 3v14h10V4H7zm5 15.5a1.2 1.2 0 100 2.4 1.2 1.2 0 000-2.4z"/></svg>
      </li>
      <li>info@yourmail.com
        <svg class="contact__icon" viewBox="0 0 24 24"><path d="M2 5h20v14H2V5zm2 2v.5l8 5.5 8-5.5V7H4zm0 3v7h16v-7l-8 5.5L4 10z"/></svg>
      </li>
      <li>www.yourwebsite.com
        <svg class="contact__icon" viewBox="0 0 24 24"><path d="M12 2a10 10 0 100 20 10 10 0 000-20zm-1 2.1V6H8.3A8 8 0 0111 4.1zM4.3 11H7c.1-1.4.3-2.7.7-3.8H5.6A8 8 0 004.3 11zm0 2a8 8 0 001.3 3.8h2.1A15 15 0 017 13H4.3zM9 13c.1 1.4.3 2.7.8 3.8H11V13H9zm0-2h2V8H9.8C9.3 9 9.1 10 9 11zm4-6.9V6h2.7A8 8 0 0013 4.1zM13 8v3h2c-.1-1-.3-2-.8-3H13zm0 5v3.8h1.2c.5-1.1.7-2.4.8-3.8h-2zm4 0c-.1 1.4-.3 2.7-.7 3.8h2.1a8 8 0 001.3-3.8H17zm0-2h2.7a8 8 0 00-1.3-3.8h-2.1c.4 1.1.6 2.4.7 3.8z"/></svg>
      </li>
    </ul>
  </section>

</main>
</body>
</html>
```